1. Overview of company:
Teal Q Amber Mobile solutions private Ltd is one of the leading innovators & providers of Value added services (VAS) and telecom solutions to the top telecom operators across the world. We are the pioneer of several telecom technologies and products with our solutions empowering over 40 telecom giant in 51 countries.

2. Product Overview:
Zippy tone is the most innovative voice morphing mobile app that has revolutionized the concept of IVR based offerings for telecom operators across the world. It lets you talk to your friend in a voice of your choice at just the press of a button. In addition to every call, users can now speak to their friends with background sounds of their choice.

In simple words: If person A calls person B, person A can choose the voice he wants B to listen, Words and sentences remain same just the voice changes. Person A can even activate a background sound for both of them while talking.

3. Objective of the design:
The purpose of this campaign is to establish Zippy tone as Innovative, Lively, Youthful, Fun mobile app generally used for spreading smiles via pranks. The primary objective is to persuade the audience to download and use Zippy Tone mobile app, as well as to spread and characterize this new app.

4. Product layout:
Page 1: Landing Page
- pictorial explanation, what Zippy Tone stands for

Page 2: Home Screen options
-Navigation to zippy tone
-Navigation to zippy backdrop

Page 3: Zippy Tone options
-Female
-Cartoon
-King
-Bunny

Page 4: Zippy backdrop options
-Romantic
-Airport
-Traffic
-Football
-Church
-Beach

5. Target Audience
The users of the mobile app will be teenager whose age ranges from 16-27. The demographics are not restricted to a particular country and will be present on global level.

6. Deliverable
- 4 Uncoded screen and icon for mobile app "Zippy Tone"
- Our company name is "Teal Q amber" , we would like to see designs that use Black and Green, at the same time its not mandatory.
-Design should communicate what the app stands for "Changing voice of caller"

Target Market(s)

User of the mobile app will be teenagers whose age ranges from 16-27. The demographics are not restricted to a particular country and will be present on global level. It's for masses.

Industry/Entity Type

Telecommunications

Requirements
Must have
• The design should be self explanatory, what the app stands for.
• Editable format for integration purpose.
Nice to have
• Would prefer Icons and very few words.
• Professional, elegant at the same time trendy designs.

```html
<!DOCTYPE html>
<html lang="en">
<head>
<meta charset="utf-8">
<title>Zippy Tone – Landing</title>
<link href="https://fonts.googleapis.com/css2?family=Open+Sans:wght@400;700&display=swap" rel="stylesheet">
<style>
  :root {
    --green: #00d13b;
    --header-dark: #202020;
    --status-black: #080808;
    --white: #ffffff;
    --ink: #2b2b2b;
    --grey-icon: #9a9a9a;
  }
  html, body {
    margin: 0;
    padding: 0;
    overflow: hidden;
    background: var(--white);
  }
  .screen {
    position: relative;
    width: 690px;
    height: 1200px;
    overflow: hidden;
    background: var(--white);
    font-family: "Open Sans", Arial, sans-serif;
  }
  .status-bar {
    position: absolute;
    left: 0; top: 0;
    width: 690px; height: 44px;
    background: var(--status-black);
  }
  .status-bar .signal { position: absolute; left: 8px; top: 10px; }
  .status-bar .battery { position: absolute; right: 10px; top: 10px; }
  .app-header {
    position: absolute;
    left: 0; top: 44px;
    width: 690px; height: 365px;
    background: var(--header-dark);
  }
  .menu-button { position: absolute; left: 33px; top: 26px; }
  .more-button { position: absolute; right: 34px; top: 24px; }
  .app-icon {
    position: absolute;
    left: 288px; top: 116px;
    width: 104px; height: 160px;
    border-radius: 52px 52px 16px 16px;
    background: var(--green);
  }
  .app-title {
    position: absolute;
    left: 0; top: 436px;
    width: 690px;
    margin: 0;
    text-align: center;
    font-size: 46px;
    font-weight: 700;
    color: var(--green);
    letter-spacing: 0.5px;
  }
  .app-tagline {
    position: absolute;
    left: 0; top: 520px;
    width: 690px;
    margin: 0;
    text-align: center;
    font-size: 32px;
    font-weight: 400;
    color: var(--ink);
  }
  .app-tagline .accent { color: var(--green); }
  .feature {
    position: absolute;
    width: 238px; height: 238px;
    border: 3px solid var(--green);
    border-radius: 50%;
    box-sizing: border-box;
    text-align: center;
  }
  .feature-number {
    display: block;
    margin-top: 28px;
    font-size: 80px;
    line-height: 88px;
    font-weight: 700;
    color: var(--green);
  }
  .feature-text {
    display: block;
    margin-top: 6px;
    font-size: 19px;
    line-height: 24px;
    color: var(--ink);
  }
  .feature-one   { left: 103px; top: 625px; }
  .feature-two   { left: 358px; top: 773px; }
  .feature-three { left: 103px; top: 923px; }
  .feature-two .feature-number,
  .feature-three .feature-number { margin-top: 34px; }
</style>
</head>
<body>
<main class="screen">
  <div class="status-bar">
    <svg class="signal" width="44" height="22" viewBox="0 0 44 22" aria-hidden="true">
      <rect x="0" y="12" width="6" height="10" fill="var(--grey-icon)"/>
      <rect x="8" y="10" width="6" height="12" fill="var(--grey-icon)"/>
      <rect x="16" y="7" width="6" height="15" fill="var(--grey-icon)"/>
      <rect x="24" y="4" width="6" height="18" fill="var(--grey-icon)"/>
      <rect x="32" y="1" width="6" height="21" fill="var(--grey-icon)"/>
    </svg>
    <svg class="battery" width="46" height="22" viewBox="0 0 46 22" aria-hidden="true">
      <rect x="1" y="1" width="39" height="20" fill="none" stroke="var(--grey-icon)" stroke-width="2"/>
      <rect x="4" y="4" width="33" height="14" fill="var(--grey-icon)"/>
      <rect x="41" y="7" width="4" height="8" fill="var(--grey-icon)"/>
    </svg>
  </div>

  <header class="app-header">
    <svg class="menu-button" width="52" height="38" viewBox="0 0 52 38" aria-label="Menu" role="img">
      <rect x="0" y="0" width="52" height="4" fill="var(--white)"/>
      <rect x="0" y="16" width="52" height="4" fill="var(--white)"/>
      <rect x="0" y="32" width="52" height="4" fill="var(--white)"/>
    </svg>
    <svg class="more-button" width="12" height="48" viewBox="0 0 12 48" aria-label="More options" role="img">
      <circle cx="6" cy="6" r="5.5" fill="var(--white)"/>
      <circle cx="6" cy="24" r="5.5" fill="var(--white)"/>
      <circle cx="6" cy="42" r="5.5" fill="var(--white)"/>
    </svg>
    <div class="app-icon" role="img" aria-label="Green microphone app icon with stars"></div>
  </header>

  <h1 class="app-title">Zippy Tone</h1>
  <p class="app-tagline">What makes the <span class="accent">Zippy Tone</span>?</p>

  <section class="feature feature-one">
    <span class="feature-number">1</span>
    <span class="feature-text">You can talk<br>on the phone<br>a strange voice</span>
  </section>
  <section class="feature feature-two">
    <span class="feature-number">2</span>
    <span class="feature-text">You can play<br>your friends</span>
  </section>
  <section class="feature feature-three">
    <span class="feature-number">3</span>
    <span class="feature-text">You have a large<br>variety of voices</span>
  </section>
</main>
</body>
</html>
```